National Mission Critical Construction Contractor needs Stationery Design to make a bold statement

We are a small commercial construction company, working primarily in mission critical facilities across the U.S.. We have exciting corporate changes going an and a new logo and office space so we need new stationery. The final design should incorporate our new logo and invoke a fresh, high-tech feel while looking simple and modern.

Industry/Entity Type

Construction

Contact Information for Business Card

We are required to list our state licensing qualifications on the back of our card.

Font styles to use
Sans Serif

Requirements
Must have
• We need to have a design for second page of stationery, envelopes both standard and with a window and for a 3 x 4 notepad.

```html
<!DOCTYPE html>
<html lang="en">
<head>
<meta charset="utf-8">
<title>North Crest Construction Management – Stationery</title>
<link href="https://fonts.googleapis.com/css2?family=Source+Sans+3:wght@400;600&display=swap" rel="stylesheet">
<style>
:root{
  --stage:#a9a7a8;
  --paper:#f4f3f1;
  --white:#ffffff;
  --blue:#1270b9;
  --blue-light:#2aa7e1;
  --green:#8dc63f;
  --ink:#4a4a4a;
  --body:#5a5a5a;
  --faint:#e6eef5;
}
*{box-sizing:border-box;margin:0;padding:0}
html,body{width:1160px;height:1200px;overflow:hidden}
body{background:var(--stage);font-family:"Source Sans 3",sans-serif;color:var(--ink);position:relative}
.sheet{position:absolute;box-shadow:0 2px 8px rgba(0,0,0,.28);overflow:hidden}
.brand{color:var(--blue);font-weight:600;white-space:nowrap;line-height:1}
.brand small{display:block;font-weight:600;letter-spacing:.18em;text-transform:uppercase}
.mark{border-radius:50%;background:var(--blue);display:inline-block}
.watermark{position:absolute;border-radius:14px;background:linear-gradient(180deg,rgba(230,238,245,.15),var(--faint))}

/* Letterhead */
.letterhead{left:70px;top:71px;width:474px;height:667px;background:var(--paper)}
.letterhead .logo{position:absolute;left:41px;top:69px;display:flex;align-items:center;gap:6px}
.letterhead .logo .mark{width:26px;height:26px}
.letterhead .logo .brand{font-size:14px}
.letterhead .logo .brand small{font-size:4.6px;margin-top:2px}
.contact{position:absolute;left:331px;top:54px;font-size:7.4px;line-height:10.8px}
.contact .gap{height:5px}
.contact li{list-style:none;display:flex;align-items:center;gap:4px}
.contact svg{width:6px;height:6px;fill:var(--blue)}
.letterhead .watermark{left:122px;top:188px;width:344px;height:344px}
.letter{position:absolute;left:46px;top:176px;width:382px}
.letter h2{font-weight:400;font-size:12px;margin-bottom:20px}
.letter p{font-size:7.3px;font-weight:400;color:var(--body);line-height:11.4px;text-align:justify;margin-bottom:11.4px}
.signoff{position:absolute;left:46px;top:457px;font-size:7px}
.signoff .sig{display:block;margin:6px 0 4px}
.signoff .who{padding-left:3px;line-height:12.6px}
.band{position:absolute;left:0;right:0;background:linear-gradient(90deg,var(--blue) 83%,var(--blue-light) 83%)}
.letterhead .band{top:627px;height:22px}
.url{color:var(--white);font-size:7.6px;letter-spacing:.55em}
.band .url{position:absolute;left:46px;top:6px}
.band .mark{position:absolute;width:19px;height:19px;background:var(--white);border:2px solid var(--blue);top:1.5px}

/* Folder */
.folder{left:580px;top:38px;width:503px;height:709px;background:var(--white)}
.folder svg.spine{position:absolute;left:0;top:0}
.folder .logo{position:absolute;left:170px;top:54px;width:220px;text-align:center}
.folder .logo .mark{width:74px;height:74px;margin-bottom:12px}
.folder .logo .brand{font-size:29px}
.folder .logo .brand small{font-size:7.6px;margin-top:6px;padding-top:4px;border-top:2px solid #c9cfd6}
.folder .watermark{left:84px;top:236px;width:342px;height:342px}
.folder .url{position:absolute;left:0;right:0;top:664px;text-align:center;color:var(--ink);padding-left:130px}

/* Envelopes */
.env-back{left:126px;top:810px;width:528px;height:238px;background:var(--paper)}
.env-back svg{position:absolute;left:0;top:0}
.env-back .flap-content{position:absolute;left:0;right:0;top:23px;text-align:center;color:var(--white);font-size:7.6px}
.env-back .mark{width:32px;height:32px;background:var(--white);margin-bottom:2px}
.env-front{left:60px;top:915px;width:529px;height:240px;background:var(--paper)}
.env-front .logo{position:absolute;left:24px;top:28px;text-align:center}
.env-front .logo .mark{width:34px;height:34px;margin-bottom:4px}
.env-front .logo .brand{font-size:14px}
.env-front .logo .brand small{font-size:4.6px;margin-top:2px}
.env-front .watermark{left:297px;top:32px;width:224px;height:168px}
.env-front .band{top:203px;height:26px}
.env-front .band span{position:absolute;left:24px;top:8px;font-size:7.6px;color:var(--white)}

/* Business cards */
.card{border-radius:8px}
.card-front{left:730px;top:784px;width:320px;height:182px;background:var(--white)}
.card-front .band{top:21px;height:41px;background:linear-gradient(90deg,var(--blue) 70%,var(--blue-light) 70%)}
.card-front .name{position:absolute;left:19px;top:8px;color:var(--white);font-weight:600;font-size:11.5px;line-height:1.2}
.card-front .name span{display:block;font-weight:400;font-size:8.6px}
.card-front .band .mark{left:222px;top:-1px;width:42px;height:42px;border-radius:50%}
.card-front .brand-line{position:absolute;right:18px;top:68px;text-align:right}
.card-front .brand-line .brand{font-size:15.5px}
.card-front .brand-line .brand small{font-size:4.8px;margin-top:2px}
.card-front .contact{left:19px;top:122px;font-size:8.4px;line-height:12px}
.card-front .contact svg{width:7px;height:7px}
.card-front .addr{position:absolute;right:18px;top:134px;text-align:right;font-size:8.4px;line-height:12px}
.card-back{left:734px;top:980px;width:318px;height:182px;background:var(--blue)}
.card-back .pattern{position:absolute;inset:0;background:linear-gradient(135deg,#2a7fc3,#1a6fb5)}
.card-back .mark{position:absolute;left:130px;top:61px;width:60px;height:60px;background:var(--blue);border:3px solid var(--white)}
.card-back .url{position:absolute;left:0;right:0;top:155px;text-align:center;font-size:8.4px}
</style>
</head>
<body>

<!-- Letterhead -->
<section class="sheet letterhead">
  <div class="watermark" role="img" aria-label="Faint brand watermark area"></div>
  <div class="logo">
    <span class="mark"></span>
    <div class="brand">NORTH CREST<small>Construction Management</small></div>
  </div>
  <ul class="contact">
    <li>4120 Cedar Hollow Road</li>
    <li>Juneau, Alaska 99801</li>
    <li class="gap"></li>
    <li><svg viewBox="0 0 10 10"><path d="M2 0l2 2-1 2 3 3 2-1 2 2-2 2C4 10 0 6 0 2z"/></svg>555 214 3086</li>
    <li><svg viewBox="0 0 10 10"><rect x="2" y="0" width="6" height="10" rx="1"/></svg>555 732 4419</li>
    <li><svg viewBox="0 0 10 10"><rect x="0" y="4" width="10" height="5"/><rect x="2" y="0" width="6" height="4"/></svg>555 608 1275</li>
    <li><svg viewBox="0 0 10 10"><rect x="0" y="2" width="10" height="7"/></svg>hello@northcrestbuild.com</li>
  </ul>
  <article class="letter">
    <h2>Dear Mr. Carter,</h2>
    <p>Lorem ipsum dolor sit amet, consectetur adipiscing elit. Donec orci purus, luctus vitae dignissim eu, iaculis sed purus. Vivamus faucibus, ipsum nec aliquet viverra, leo mauris condimentum ligula, sit amet sagittis enim ligula quis arcu. Nam egestas tortor id nisi porttitor mattis. In tortor ante, ultricies in suscipit a, tempus non massa. Vivamus et auctor mi. Fusce vel massa nulla. Phasellus nec eros mauris, et scelerisque orci.</p>
    <p>Donec malesuada orci vitae nulla accumsan porta a id massa. Quisque accumsan iaculis magna sit amet fringilla. Maecenas consequat, magna eget tincidunt semper, odio nibh rutrum mi, id feugiat ante nisi eu risus. Vestibulum nunc orci, rhoncus a placerat in, ultricies in mi. Cras mattis varius eros, vel fringilla nisi suscipit eget. Quisque scelerisque sagittis nulla at porttitor.</p>
    <p>Sed id augue vitae urna euismod commodo aliquet a quam. Pellentesque arcu velit, cursus et malesuada ut, consequat et diam. Nullam erat sem, rhoncus id ullamcorper vitae, rhoncus et arcu. In ultricies ultricies nulla, ut rutrum nisi iaculis at. Donec eu magna a metus ornare faucibus. Fusce aliquet faucibus ultricies. Morbi semper, est id tincidunt gravida, sem arcu adipiscing lacus, ac bibendum nulla leo eu purus. Quisque nec diam sed risus consectetur a cumsan quis quis nibh. Vestibulum id purus lorem.</p>
    <p>It is a long established fact that a reader will be distracted by the readable content of a page when looking at its layout. The point of using Lorem Ipsum is that it has a more-or-less normal distribution of letters, as opposed to using 'Content here, content here', making it look like readable English. Many desktop publishing packages</p>
  </article>
  <div class="signoff">
    Sincerely,
    <svg class="sig" width="64" height="24" viewBox="0 0 64 24" fill="none" stroke="#222" stroke-width=".9"><path d="M0 12c14-1 30-1 44-2M18 4c8 0 14 2 12 6s-6 10-4 12M30 10c8 2 20 4 30 6"/></svg>
    <div class="who">Daniel Reyes<br>CEO/ Founder</div>
  </div>
  <div class="band"><span class="url">www.northcrestbuild.com</span><span class="mark" style="left:404px"></span></div>
</section>

<!-- Presentation folder -->
<section class="sheet folder">
  <svg class="spine" width="60" height="709" viewBox="0 0 60 709">
    <path d="M0 0H38C62 90 62 200 46 300S18 520 26 620 36 690 42 709H0Z" fill="var(--blue)"/>
    <path d="M38 0C62 90 62 200 46 300S18 520 26 620 36 690 42 709" fill="none" stroke="var(--green)" stroke-width="4"/>
    <path d="M38 0C60 90 59 200 43 300S15 520 23 620 33 690 39 709" fill="none" stroke="var(--white)" stroke-width="1.5"/>
  </svg>
  <div class="watermark" role="img" aria-label="Faint brand watermark area"></div>
  <div class="logo">
    <span class="mark"></span>
    <div class="brand">NORTH CREST<small>Construction Management</small></div>
  </div>
  <span class="url">www.northcrestbuild.com</span>
</section>

<!-- Envelope, back -->
<section class="sheet env-back">
  <svg width="528" height="238" viewBox="0 0 528 238">
    <path d="M0 0H528L520 60Q515 88 485 88H43Q13 88 10 60Z" fill="var(--blue)"/>
  </svg>
  <div class="flap-content"><span class="mark"></span><br>www.northcrestbuild.com</div>
</section>

<!-- Envelope, front -->
<section class="sheet env-front">
  <div class="watermark" role="img" aria-label="Faint brand watermark area"></div>
  <div class="logo">
    <span class="mark"></span>
    <div class="brand">NORTH CREST<small>Construction Management</small></div>
  </div>
  <div class="band"><span>4120 Cedar Hollow Road, Juneau, Alaska 99801</span><span class="mark" style="left:448px;top:3px"></span></div>
</section>

<!-- Business card, front -->
<section class="sheet card card-front">
  <div class="band">
    <div class="name">DANIEL REYES<span>CEO/Founder</span></div>
    <span class="mark" style="position:absolute"></span>
  </div>
  <div class="brand-line"><div class="brand">NORTH CREST<small>Construction Management</small></div></div>
  <ul class="contact">
    <li><svg viewBox="0 0 10 10"><path d="M2 0l2 2-1 2 3 3 2-1 2 2-2 2C4 10 0 6 0 2z"/></svg>555 214 3086</li>
    <li><svg viewBox="0 0 10 10"><rect x="2" y="0" width="6" height="10" rx="1"/></svg>555 732 4419</li>
    <li><svg viewBox="0 0 10 10"><rect x="0" y="4" width="10" height="5"/><rect x="2" y="0" width="6" height="4"/></svg>555 608 1275</li>
    <li><svg viewBox="0 0 10 10"><rect x="0" y="2" width="10" height="7"/></svg>hello@northcrestbuild.com</li>
  </ul>
  <div class="addr">4120 Cedar Hollow Road<br>Juneau, Alaska 99801<br>www.northcrestbuild.com</div>
</section>

<!-- Business card, back -->
<section class="sheet card card-back">
  <div class="pattern" role="img" aria-label="Repeating decorative pattern in two tones of blue"></div>
  <span class="mark"></span>
  <span class="url">www.northcrestbuild.com</span>
</section>

</body>
</html>
```